Corvel Capital LLC

Need Professional Business cards for New Investment Fund

Target Market(s)

High Quality investors

Industry/Entity Type

Financial

Contact Information for Business Card

Phone Number +1 555 284 6190
Name Lukas Varenko
Title Fund Manager
email lv@FundCorvel.com
Website www.FundCorvel.com

Colors

Designer to choose colors to be used in the design.

Requirements
Must have
• Must have our Logo and all of the above. Must be made so lettering and loge can be raised

```html
<!DOCTYPE html>
<html lang="en">
<head>
<meta charset="utf-8">
<title>Quelmara — Business Card</title>
<link rel="stylesheet" href="https://fonts.googleapis.com/css2?family=Roboto:wght@400;500&display=swap">
<style>
  :root {
    --backdrop: #2a2a2a;
    --card: #161616;
    --mark-embossed: #3a3a3a;
    --mark-light: #ececec;
    --accent: #8dc21f;
    --text: #d6d6d6;
  }
  * { margin: 0; padding: 0; box-sizing: border-box; }
  html, body {
    width: 1200px;
    height: 1138px;
    overflow: hidden;
    background: var(--backdrop);
    font-family: "Roboto", Arial, sans-serif;
  }
  .card {
    position: absolute;
    left: 274px;
    width: 622px;
    height: 373px;
    background: var(--card);
    border-radius: 14px;
  }
  .card--front { top: 186px; }
  .card--back { top: 608px; }

  .wordmark {
    position: absolute;
    font-weight: 500;
    letter-spacing: 1px;
    line-height: 1;
    white-space: nowrap;
  }
  .card--front .wordmark {
    left: 0;
    right: 0;
    top: 152px;
    text-align: center;
    font-size: 68px;
    color: var(--mark-embossed);
  }
  .card--back .wordmark {
    right: 26px;
    top: 96px;
    font-size: 50px;
    color: var(--mark-light);
    display: flex;
    align-items: center;
    gap: 12px;
  }
  .wordmark__square {
    width: 14px;
    height: 14px;
    background: var(--accent);
  }

  .holder {
    position: absolute;
    left: 26px;
    top: 264px;
  }
  .holder__name {
    font-size: 24px;
    font-weight: 500;
    color: var(--accent);
    line-height: 1.1;
  }
  .holder__title {
    font-size: 16px;
    color: var(--text);
    margin-top: 3px;
  }
  .divider {
    position: absolute;
    left: 26px;
    right: 26px;
    top: 322px;
    height: 1px;
    background: var(--accent);
  }
  .contacts {
    position: absolute;
    left: 26px;
    right: 26px;
    top: 332px;
    display: flex;
    justify-content: space-between;
    font-size: 16px;
    color: var(--text);
  }
  .contacts__item {
    display: flex;
    align-items: center;
    gap: 10px;
  }
  .contacts__icon { width: 15px; height: 15px; fill: var(--accent); }
</style>
</head>
<body>
  <section class="card card--front">
    <div class="wordmark">QUELMARA</div>
  </section>

  <section class="card card--back">
    <div class="wordmark"><span class="wordmark__square"></span>QUELMARA</div>

    <div class="holder">
      <div class="holder__name">Lukas Varenko</div>
      <div class="holder__title">Fund Manager</div>
    </div>

    <div class="divider"></div>

    <div class="contacts">
      <span class="contacts__item">
        <svg class="contacts__icon" viewBox="0 0 16 16" aria-hidden="true">
          <path d="M1 6c0-2 3-3 7-3s7 1 7 3v1h-4V6H5v1H1z"/>
          <path d="M4 8h8l2 5H2z"/>
        </svg>
        +1 555 284 6190
      </span>
      <span class="contacts__item">
        <svg class="contacts__icon" viewBox="0 0 16 16" aria-hidden="true">
          <rect x="1" y="3" width="14" height="10"/>
          <path d="M1.5 3.5L8 9l6.5-5.5" stroke="#161616" stroke-width="1.2" fill="none"/>
        </svg>
        lv@FundCorvel.com
      </span>
      <span class="contacts__item">
        <svg class="contacts__icon" viewBox="0 0 16 16" aria-hidden="true">
          <circle cx="8" cy="8" r="7"/>
          <path d="M1 8h14M8 1v14M3 4.5h10M3 11.5h10" stroke="#161616" stroke-width="1" fill="none"/>
        </svg>
        www.FundCorvel.com
      </span>
    </div>
  </section>
</body>
</html>
```